Kelvor Engineers: Why you should hire us keepsake

New design. Open to plastic cards. We are an engineering firm that designs cell phone towers and commercial buildings. Please check out our website www.kelvorstruct.com for more details. We want people to remember our card and for it to be useful if possible. We want the same look and feel on these cards to be translated to other marketing material we may need such as brochures.

Target Market(s)

Architects, Developers and Telecommunication Carriers

Industry/Entity Type

Engineering

Contact Information for Business Card

Card with our company colors, logo, and innovative design with elements related to our industry.

Font styles to use
Sans Serif

Colors
9bcb3c
abd036
0255a3

Requirements
Must have
• Sleek and hip design
Nice to have
• Bright lime green and navy coloring that pops with an innovative design.
Should not have
• A basic and boring design

```html
<!DOCTYPE html>
<html lang="en">
<head>
<meta charset="utf-8">
<title>Kelvor Engineers – Business Card</title>
<link rel="stylesheet" href="https://fonts.googleapis.com/css2?family=Roboto+Condensed:wght@700&family=Roboto:wght@400;700&display=swap">
<style>
  :root {
    --lime: #1ff21f;
    --navy: #002d5c;
    --navy-line: #7f93ad;
    --ink-grey: #555a5e;
    --card-white: #f4f4f4;
    --backdrop: #e6e7e9;
    --text-white: #ffffff;
  }
  * { margin: 0; padding: 0; box-sizing: border-box; }
  html, body {
    width: 1200px; height: 960px; overflow: hidden;
    background: var(--backdrop);
  }
  .canvas { position: relative; width: 1200px; height: 960px; }

  .card {
    position: absolute; left: 320px; width: 600px;
    border-radius: 18px;
  }
  .card--front {
    top: 102px; height: 348px; background: var(--card-white);
  }
  .card--back {
    top: 493px; height: 342px; background: var(--navy);
  }

  .brand-name {
    position: absolute; left: 0; right: 0; top: 118px;
    text-align: center;
    font-family: "Roboto Condensed", sans-serif; font-weight: 700;
    font-size: 96px; line-height: 1; letter-spacing: 1px;
    color: var(--lime);
  }
  .tagline {
    position: absolute; left: 0; right: 0; top: 272px;
    display: flex; justify-content: center; align-items: center; gap: 2px;
    font-family: "Roboto", sans-serif; font-weight: 700;
    font-size: 15px; color: var(--lime);
  }
  .tagline__rule { width: 28px; height: 2px; background: var(--navy); }
  .locations {
    position: absolute; left: 0; right: 0; top: 294px;
    text-align: center;
    font-family: "Roboto", sans-serif; font-size: 15px;
    color: var(--ink-grey); letter-spacing: 0.9px;
  }

  .person-name {
    position: absolute; right: 38px; top: 31px;
    font-family: "Roboto Condensed", sans-serif; font-weight: 700;
    font-size: 21px; color: var(--lime);
  }
  .divider {
    position: absolute; left: 40px; top: 267px; width: 525px; height: 1px;
    background: linear-gradient(to right, var(--navy-line), rgba(127,147,173,0));
  }
  .contacts {
    position: absolute; top: 279px; display: grid; row-gap: 2px;
    font-family: "Roboto", sans-serif; font-size: 14px; color: var(--text-white);
  }
  .contacts--phones { left: 38px; }
  .contacts--web { left: 185px; }
  .contact { display: flex; align-items: center; gap: 8px; height: 18px; }
  .contact__icon { width: 12px; height: 12px; fill: var(--lime); flex: none; }
</style>
</head>
<body>
<div class="canvas">

  <section class="card card--front">
    <div class="brand-name">KELVOR</div>
    <div class="tagline">
      <span class="tagline__rule"></span>
      <span>MULTI-DISCIPLINE ENGINEERING</span>
      <span class="tagline__rule"></span>
    </div>
    <div class="locations">Savannah | Raleigh | Austin | Knoxville</div>
  </section>

  <section class="card card--back">
    <div class="person-name">DANA HOLLOWAY BRISK</div>
    <div class="divider"></div>

    <div class="contacts contacts--phones">
      <div class="contact">
        <svg class="contact__icon" viewBox="0 0 12 12" aria-hidden="true"><path d="M2.4 0.5 4.3 2.6 3.3 4.1Q4.4 6.6 7.9 8.7L9.4 7.7 11.5 9.6 10.1 11.5Q5.6 11.2 0.5 1.9Z"/></svg>
        <span>555.014.7310</span>
      </div>
      <div class="contact">
        <svg class="contact__icon" viewBox="0 0 12 12" aria-hidden="true"><path d="M3 0h6a1 1 0 0 1 1 1v10a1 1 0 0 1-1 1H3a1 1 0 0 1-1-1V1a1 1 0 0 1 1-1Zm0.6 1.4v8.2h4.8V1.4Z"/></svg>
        <span>555.019.2046</span>
      </div>
    </div>

    <div class="contacts contacts--web">
      <div class="contact">
        <svg class="contact__icon" viewBox="0 0 12 12" aria-hidden="true"><path d="M0 2h12v1.2L6 7 0 3.2ZM0 4.6l6 3.8 6-3.8V10H0Z"/></svg>
        <span>dbrisk@kelvorstruct.com</span>
      </div>
      <div class="contact">
        <svg class="contact__icon" viewBox="0 0 12 12" aria-hidden="true"><circle cx="6" cy="6" r="6"/><path d="M3 3.5q2 0 2.5 1.5t-1 2.5L4 10 6.5 9 8 7 7 5.5 9 3.5" fill="none" stroke="#002d5c" stroke-width="1"/></svg>
        <span>www.kelvorstruct.com</span>
      </div>
    </div>
  </section>

</div>
</body>
</html>
```